Business Card Design needed for start up company Halvora

In need of a new business card designed for a start up company based in Sydney, Halvora is a new start up innovative Company, our mission it to make property accessible for everyday Australian and to become the leading Real Estate platform in Australia. We want it to be fresh and clean.

Industry/Entity Type

Financial

Contact Information for Business Card

Section for Name
Section for Title

HALVORA - The Strength of Pooling
Mobile:
Direct:

Font styles to use
Sans Serif

Colors
33a6d7
0692cd
0255a3
ffffff

Requirements
Must have
• Logo, all business card details

```html
<!DOCTYPE html>
<html lang="en">
<head>
<meta charset="utf-8">
<title>Halvora Business Card</title>
<link rel="stylesheet" href="https://fonts.googleapis.com/css2?family=Jost:wght@400;500;600&display=swap">
<style>
  :root {
    --sky: #33a6d7;
    --azure: #0692cd;
    --royal: #0255a3;
    --white: #ffffff;
    --navy-deep: #0b1a3d;
    --wordmark: #0255a3;
    --tagline: #5a6b80;
    --frost-light: #f3f5f7;
    --frost-shade: #dfe4e8;
    --backdrop: #e9e6e2;
    --muted-white: #dfe6f2;
  }
  * { margin: 0; padding: 0; box-sizing: border-box; }
  html, body {
    width: 1200px;
    height: 970px;
    overflow: hidden;
    background: var(--backdrop);
    font-family: "Jost", "Futura", sans-serif;
  }
  .canvas {
    position: relative;
    width: 1200px;
    height: 970px;
  }
  .card {
    position: absolute;
    left: 100px;
    top: 200px;
    width: 1000px;
    height: 570px;
    border-radius: 24px;
    overflow: hidden;
    background: linear-gradient(160deg, var(--frost-light) 0%, var(--frost-shade) 100%);
    box-shadow: 0 10px 30px rgba(0, 0, 0, 0.12);
  }
  .card-shapes {
    position: absolute;
    inset: 0;
    width: 1000px;
    height: 570px;
  }
  .brand {
    position: absolute;
    left: 70px;
    top: 238px;
    width: 400px;
  }
  .brand-name {
    font-size: 60px;
    font-weight: 500;
    letter-spacing: 4px;
    color: var(--wordmark);
    line-height: 1;
  }
  .brand-tagline {
    margin-top: 12px;
    font-size: 18px;
    font-weight: 400;
    letter-spacing: 0.6px;
    color: var(--tagline);
  }
  .details {
    position: absolute;
    left: 646px;
    top: 126px;
    color: var(--muted-white);
  }
  .person-name {
    font-size: 33px;
    font-weight: 600;
    color: var(--azure);
    letter-spacing: 0.5px;
    line-height: 1.1;
  }
  .person-title {
    font-size: 26px;
    font-weight: 400;
    letter-spacing: 0.5px;
    margin-top: 4px;
  }
  .address {
    margin-top: 20px;
    font-size: 23px;
    line-height: 29px;
    letter-spacing: 0.4px;
  }
  .contact-list {
    list-style: none;
    margin-top: 16px;
  }
  .contact-item {
    display: flex;
    align-items: center;
    gap: 12px;
    height: 34px;
    font-size: 22px;
    letter-spacing: 0.3px;
  }
  .contact-icon {
    width: 24px;
    height: 24px;
    flex: none;
  }
</style>
</head>
<body>
<main class="canvas">
  <section class="card" aria-label="Halvora business card">
    <svg class="card-shapes" viewBox="0 0 1000 570" aria-hidden="true">
      <defs>
        <linearGradient id="panelFill" x1="0" y1="0" x2="1" y2="1">
          <stop offset="0" stop-color="#1b3368"/>
          <stop offset="0.55" stop-color="#0f2150"/>
          <stop offset="1" stop-color="#0a1838"/>
        </linearGradient>
      </defs>
      <path class="edge-crescent" fill="#0255a3"
            d="M745 0 C545 40 455 300 500 440 C525 510 565 550 605 570 L1000 570 L1000 0 Z"/>
      <path class="info-panel" fill="url(#panelFill)"
            d="M770 0 C575 40 480 300 525 440 C550 510 590 550 630 570 L1000 570 L1000 0 Z"/>
    </svg>

    <div class="brand">
      <p class="brand-name">HALVORA</p>
      <p class="brand-tagline">The Strength of Pooling</p>
    </div>

    <div class="details">
      <p class="person-name">MARA LINDQVIST</p>
      <p class="person-title">CEO/FOUNDER</p>
      <p class="address">214 Harbour View Road<br>Sydney, NSW 2000</p>
      <ul class="contact-list">
        <li class="contact-item">
          <svg class="contact-icon" viewBox="0 0 24 24"><circle cx="12" cy="12" r="12" fill="#33a6d7"/><path d="M8 6.5l2 2.3-1.1 1.4a8 8 0 0 0 4.9 4.9l1.4-1.1 2.3 2-1.3 1.6c-4.6-.6-8.5-4.5-9.1-9.1z" fill="#0b1a3d"/></svg>
          <span>612 480 3317</span>
        </li>
        <li class="contact-item">
          <svg class="contact-icon" viewBox="0 0 24 24"><circle cx="12" cy="12" r="12" fill="#33a6d7"/><rect x="8.5" y="5" width="7" height="14" rx="1.3" fill="#0b1a3d"/><rect x="9.7" y="7" width="4.6" height="8.5" fill="#33a6d7"/></svg>
          <span>041 275 8806</span>
        </li>
        <li class="contact-item">
          <svg class="contact-icon" viewBox="0 0 24 24"><circle cx="12" cy="12" r="12" fill="#33a6d7"/><rect x="6" y="8" width="12" height="8.5" rx="1" fill="#0b1a3d"/><path d="M6.5 8.5l5.5 4.3 5.5-4.3" stroke="#33a6d7" stroke-width="1.2" fill="none"/></svg>
          <span>mara@halvora.com</span>
        </li>
        <li class="contact-item">
          <svg class="contact-icon" viewBox="0 0 24 24"><circle cx="12" cy="12" r="12" fill="#33a6d7"/><circle cx="12" cy="12" r="6" fill="none" stroke="#0b1a3d" stroke-width="1.4"/><ellipse cx="12" cy="12" rx="2.6" ry="6" fill="none" stroke="#0b1a3d" stroke-width="1.2"/><path d="M6 12h12" stroke="#0b1a3d" stroke-width="1.2"/></svg>
          <span>www.halvora.com</span>
        </li>
      </ul>
    </div>
  </section>
</main>
</body>
</html>
```